Mobile welding fabrication and repair, heavy equipment and semi repair

We need a business card design that will catch the eye but look prelesional at the same time. Were based out of Idaho and we do all welding fabrication jobs and repairs, we also build and install custom pipe fences for personal or larger scale fence jobs and can give free quotes. We can do semi truck and trailer repairs Mobily also.

Target Market(s)

Welding

Industry/Entity Type

welding and repair

Contact Information for Business Card

email (ravenforgeandmend@mailbay.net, phone number 208-417-3826, owner (Dalton Whitcomb), Pipe Fence, Semi Repair, Mobile welding and fabrication

Font styles to use
Sans Serif

Requirements
Must have
• My logo in black background on one side , and other side my logo in white back round with all the information listed on card details
Nice to have
• make it stand out from other business cards

```html
<!DOCTYPE html>
<html lang="en">
<head>
<meta charset="utf-8">
<title>Raven Forge and Mend — Business Card</title>
<link rel="stylesheet" href="https://fonts.googleapis.com/css2?family=Lato:wght@400;700;900&display=swap">
<style>
  :root {
    --stage: #2a2a2b;
    --card-white: #f7f8f9;
    --card-black: #151515;
    --brand-blue: #1a73c9;
    --ink: #2b2b2b;
    --muted: #555a60;
    --rule: #d3d6da;
    --steel: #c9ccd0;
    --service: #e6e8ea;
  }
  * { box-sizing: border-box; margin: 0; padding: 0; }
  html, body {
    width: 1200px; height: 900px; overflow: hidden;
    background: var(--stage);
    font-family: "Lato", Arial, sans-serif;
  }
  .sheet {
    width: 1200px; height: 900px;
    display: flex; flex-direction: column; align-items: center; justify-content: center;
    gap: 40px;
  }
  .card {
    position: relative;
    width: 700px; height: 400px;
    border-radius: 4px;
    box-shadow: 0 14px 30px rgba(0,0,0,.45);
  }
  .card--front { background: var(--card-white); }
  .card--back { background: var(--card-black); }

  .brand {
    position: absolute;
    font-weight: 900;
    letter-spacing: 1px;
    line-height: 1;
    white-space: nowrap;
  }
  .card--front .brand {
    right: 64px; top: 70px;
    font-size: 40px;
    color: var(--brand-blue);
  }
  .card--back .brand {
    left: 0; right: 0; top: 150px;
    text-align: center;
    font-size: 46px;
    color: var(--steel);
  }

  .divider {
    position: absolute;
    left: 110px; right: 40px; top: 190px;
    height: 1px; background: var(--rule);
  }

  .contact {
    position: absolute;
    left: 70px; bottom: 48px;
  }
  .contact__name {
    font-size: 30px; font-weight: 700;
    color: var(--brand-blue);
    letter-spacing: .5px;
    text-transform: uppercase;
  }
  .contact__role {
    font-size: 20px; color: var(--muted);
    margin: 2px 0 0 14px;
  }
  .contact__rule {
    width: 420px; height: 1px; background: var(--rule);
    margin: 14px 0 14px 14px;
  }
  .contact__line {
    display: flex; align-items: center; gap: 10px;
    font-size: 21px; color: var(--ink);
    margin-left: 30px; line-height: 1.35;
  }
  .contact__line svg { width: 20px; height: 20px; flex: none; }

  .services {
    position: absolute;
    left: 0; right: 0; bottom: 70px;
    display: flex; justify-content: center; align-items: center; gap: 10px;
    font-size: 17px; letter-spacing: .3px;
    color: var(--service);
    text-transform: uppercase;
  }
  .services__dot {
    width: 8px; height: 8px; border-radius: 50%;
    background: var(--brand-blue);
  }
</style>
</head>
<body>
<main class="sheet">
  <section class="card card--front" aria-label="Card front">
    <div class="brand">RAVEN FORGE AND MEND</div>
    <div class="divider"></div>
    <div class="contact">
      <div class="contact__name">Dalton Whitcomb</div>
      <div class="contact__role">Owner</div>
      <div class="contact__rule"></div>
      <div class="contact__line">
        <svg viewBox="0 0 20 20" aria-hidden="true"><path fill="var(--brand-blue)" d="M5 2l3 4-2 2c1 2.5 3.5 5 6 6l2-2 4 3-2 3C9 18 2 11 2 4z"/></svg>
        <span>208-417-3826</span>
      </div>
      <div class="contact__line">
        <svg viewBox="0 0 20 20" aria-hidden="true"><rect x="1" y="4" width="18" height="12" fill="var(--brand-blue)"/><path d="M1 4l9 7 9-7" fill="none" stroke="#fff" stroke-width="1.5"/></svg>
        <span>ravenforgeandmend@mailbay.net</span>
      </div>
    </div>
  </section>

  <section class="card card--back" aria-label="Card back">
    <div class="brand">RAVEN FORGE AND MEND</div>
    <div class="services">
      <span>Pipe Fence</span><span class="services__dot"></span>
      <span>Semi Repair</span><span class="services__dot"></span>
      <span>Mobile Welding</span><span class="services__dot"></span>
      <span>Fabrication</span>
    </div>
  </section>
</main>
</body>
</html>
```